NZ First of it's kind solutions directory and marketplace for busy Mums needs a business card design

We need a business card design for our new nationwide business in NZ (long term plans to go global). We provide solutions to the everyday challenges that busy Mums face by connecting them with quality communities and suppliers of carefully selected, relevant products and services. We sell direct via our online marketplace. The final design should communicate our values of inclusivity, quality and smart solutions. Colours should incorporate our logo colour palette of #477077 and #6ba8b2. Our website is at https://www.brightnestmums.example

Target Market(s)

busy Mums, Age 28 – 50, female, income over $100K, location main centres NZ primarily but NZ wide. Is likely juggling work or career with a young family. Probably had hobbies which have fallen by the wayside.
-Wants to succeed in her chosen career without compromising on family life
-to successfully juggle her career without feeling like she is compromising her children
- Is time poor, something always has to give and it’s generally her health (she’ll stay up late, get stressed)
- probably ex corporate or professional career. Has discretional income

Industry/Entity Type

Business

Contact Information for Business Card

Lena Forbisher, Founder, BrightNestMums.example (Strapline Tap; Gather; Sorted), 47 Kowhai Terrace, Ellerslie, Auckland 1051, New Zealand. Mob: 021 483 517 Ph: +64 (0)9 571 4860

Font styles to use
Other font styles liked:
• Raleway, and/or Architects Daughter

Colors
00a990
33b8a4
86cfc6
cfeae6

Requirements
Must have
• the above details, streamline. the logo and colours associated with those logos
Should not have
• foil or metallic colours

```html
<!DOCTYPE html>
<html lang="en">
<head>
<meta charset="utf-8">
<title>BrightNestMums – Business Card</title>
<link rel="stylesheet" href="https://fonts.googleapis.com/css2?family=Arimo:wght@400;700&display=swap">
<style>
  :root {
    --stage: #939393;
    --card-light: #ffffff;
    --card-dark: #232323;
    --brand-deep: #477077;
    --brand-light: #6ba8b2;
    --ink: #222222;
    --ink-soft: #444444;
    --rule: #c9c9c9;
  }
  * { margin: 0; padding: 0; box-sizing: border-box; }
  html, body { width: 1200px; height: 900px; overflow: hidden; }
  body {
    background: var(--stage);
    font-family: "Arimo", Arial, sans-serif;
    position: relative;
  }
  .card {
    position: absolute;
    top: 275px;
    width: 478px;
    height: 295px;
  }
  .card--front {
    left: 116px;
    background: var(--card-light);
    border-radius: 0 58px 0 58px;
  }
  .card--back {
    left: 622px;
    background: var(--card-dark);
    border-radius: 58px 0 58px 0;
  }
  .brand {
    position: absolute;
    left: 156px;
    top: 80px;
    display: flex;
    align-items: center;
    gap: 10px;
  }
  .brand__dot {
    width: 30px; height: 30px;
    border-radius: 50%;
    background: var(--brand-deep);
  }
  .brand__name {
    font-size: 30px;
    font-weight: 700;
    color: var(--brand-deep);
    letter-spacing: -0.5px;
  }
  .person {
    position: absolute;
    left: 29px;
    top: 167px;
    right: 26px;
  }
  .person__name {
    font-size: 18px;
    font-weight: 700;
    color: var(--ink-soft);
    letter-spacing: 0.3px;
  }
  .person__first { color: var(--brand-deep); }
  .person__role-row {
    display: flex;
    align-items: center;
    gap: 7px;
    margin-top: 1px;
  }
  .person__role { font-size: 13px; color: var(--ink); }
  .person__rule { flex: 1; height: 1px; background: var(--rule); }
  .contact {
    position: absolute;
    left: 29px;
    top: 214px;
    list-style: none;
    font-size: 13.5px;
    color: var(--ink);
    line-height: 17.5px;
  }
  .contact li { display: flex; align-items: center; gap: 4px; }
  .contact svg { width: 11px; height: 11px; fill: var(--ink-soft); }
  .address {
    position: absolute;
    right: 26px;
    top: 231px;
    font-style: normal;
    text-align: right;
    font-size: 13.5px;
    line-height: 17.5px;
    color: var(--ink);
  }
  .back-mark {
    position: absolute;
    left: 50%;
    top: 68px;
    transform: translateX(-50%);
    display: flex;
    flex-direction: column;
    align-items: center;
    gap: 18px;
  }
  .back-mark__dot {
    width: 96px; height: 96px;
    border-radius: 50%;
    background: var(--brand-deep);
  }
  .back-mark__name {
    font-size: 24px;
    font-weight: 700;
    color: var(--brand-deep);
  }
  .back-url {
    position: absolute;
    left: 0; right: 0;
    top: 242px;
    text-align: center;
    font-size: 14px;
    letter-spacing: 1.8px;
    color: var(--brand-light);
  }
</style>
</head>
<body>

<section class="card card--front" aria-label="Card front">
  <div class="brand">
    <span class="brand__dot"></span>
    <span class="brand__name">BrightNestMums</span>
  </div>

  <div class="person">
    <p class="person__name"><span class="person__first">LENA</span> FORBISHER</p>
    <div class="person__role-row">
      <span class="person__role">Founder</span>
      <span class="person__rule"></span>
    </div>
  </div>

  <ul class="contact">
    <li>
      <svg viewBox="0 0 12 12" aria-hidden="true"><path d="M1 4c0-2 2-3 5-3s5 1 5 3v1H8V4H4v1H1zM3 6h6l1.5 5h-9z"/></svg>
      021 483 517
    </li>
    <li>
      <svg viewBox="0 0 12 12" aria-hidden="true"><path d="M3 0h6a1 1 0 0 1 1 1v10a1 1 0 0 1-1 1H3a1 1 0 0 1-1-1V1a1 1 0 0 1 1-1zm0 1.5v8h6v-8z"/></svg>
      +64 (0)9 571 4860
    </li>
    <li>
      <svg viewBox="0 0 12 12" aria-hidden="true"><circle cx="6" cy="6" r="5.5"/><path d="M6 .5v11M.5 6h11" stroke="#fff" stroke-width="0.8"/></svg>
      www.BrightNestMums.example
    </li>
  </ul>

  <address class="address">
    47 Kowhai Terrace, Ellerslie<br>
    Auckland 1051, New Zealand
  </address>
</section>

<section class="card card--back" aria-label="Card back">
  <div class="back-mark">
    <span class="back-mark__dot"></span>
    <span class="back-mark__name">BrightNestMums</span>
  </div>
  <p class="back-url">www.BrightNestMums.example</p>
</section>

</body>
</html>
```